Website redesign for KestrelFinanceMan/TKFinanceMan

Job Title: Talented Web Designer for SEO-Friendly Website Creation & HostFalcon cPanel Integration
 
Inspiration: dunewheelracingexample.com
Pages:

About
Get a Quote
FAQ
Boat Loans
RV Loans
Testimonials
News/Blog
Affiliate Program
Contact

Job Description:
 
We are seeking a skilled and creative freelance web designer to build a stunning, SEO-optimized website for our business. The ideal candidate will have a strong design portfolio, technical expertise in creating search engine-friendly websites, and experience implementing websites into HostFalcon cPanel.
 
Project Overview:
 
Objective: Create a modern, motorsports themed visually appealing website that is optimized for SEO.

Platform: The site will be hosted on HostFalcon, so familiarity with their cPanel for setup and integration is essential.

Deliverables:
         •A fully functional website (desktop and mobile) with user-friendly navigation and a responsive design.
         •SEO best practices implemented throughout, including proper meta tags, optimized images, fast loading speeds, and mobile compatibility.
         •Seamless integration into HostFalcon cPanel for hosting.
         •Guidance or documentation on maintaining the site post-launch.
 
Key Skills Required:
 
         •Proficiency in web design (HTML, CSS, JavaScript, or relevant platforms like WordPress).
         •Knowledge of SEO principles and tools for website optimization.
         •Experience with HostFalcon cPanel, including file management and DNS settings.
         •Strong communication skills to understand our vision and provide progress updates.
 
What We’re Looking For:
 
         •A designer who can transform our ideas into a sleek and functional website.
         •Someone proactive in suggesting creative design elements and SEO improvements.
         •A reliable professional who can meet deadlines and deliver a polished product.
 
Please provide:
 
         1.A brief introduction and why you’re a good fit for this project.
         2.Examples of previous web design projects, especially those with SEO implementation.
         3.Your estimated timeline and cost for this project.
 
We are excited to work with a talented designer who can bring our vision to life. If you are passionate about web design and SEO, we’d love to hear from you!

Target Market(s)

Boat and RV buyers looking for a loan

Coding

Coded - Design and coding required

Number of Pages Required

5+ page

Colors
F0912C
F2A743
F7CA91
FBE8D2
FDF5EE

Requirements
Must have
• motorsports type design
Nice to have
• fcontact forms easy to use layout on brand and color scheme of kestrelfinanceman and tkfinanceman.example

```html
<!DOCTYPE html>
<html lang="en">
<head>
<meta charset="utf-8">
<title>KestrelFinanceMan — Boat Loans Made Easy</title>
<link href="https://fonts.googleapis.com/css2?family=Lexend:wght@300;400;500;600&display=swap" rel="stylesheet">
<style>
:root{
  --orange:#ff6a06;
  --orange-soft:#f0912c;
  --ink:#1b1b1b;
  --text:#444;
  --white:#fff;
  --footer:#2c2c2c;
  --line:#e6e6e6;
  --field:#f3f3f3;
  --star:#ffb21a;
}
*{box-sizing:border-box;margin:0;padding:0}
html,body{width:1200px;height:2957px;overflow:hidden}
body{position:relative;font-family:'Lexend',sans-serif;color:var(--ink);background:var(--white)}
.abs{position:absolute}
.accent{color:var(--orange)}
.underline-link{font-weight:500;text-transform:uppercase;text-decoration:none;color:inherit;border-bottom:3px solid var(--orange);padding-bottom:2px}

/* header + hero */
.hero{left:0;top:0;width:1200px;height:500px;background:linear-gradient(180deg,#6f88a6 0%,#9fb4c8 45%,#3c5a3c 56%,#5a7ea1 66%,#6f93b4 100%)}
.hero-shade{left:0;top:0;width:1200px;height:500px;background:linear-gradient(90deg,rgba(30,40,60,.55),rgba(30,40,60,0) 60%)}
.brand{left:75px;top:34px;display:flex;align-items:center;gap:9px;color:var(--orange);font-weight:600;font-size:17px;white-space:nowrap}
.brand-dot{width:14px;height:14px;border-radius:50%;background:var(--white);flex:none}
.nav{left:360px;top:40px;display:flex;gap:19px;align-items:center;font-size:11.5px;font-weight:500;color:var(--white);text-transform:uppercase;white-space:nowrap}
.hero-title{left:107px;top:146px;font-size:30px;font-weight:600;color:var(--white)}
.hero-text{left:109px;top:200px;width:500px;font-size:15px;line-height:33px;color:var(--white);font-weight:300}
.hero-cta{left:109px;top:277px;font-size:16px;color:var(--white)}

.calc{left:180px;top:448px;width:840px;height:118px;background:var(--white);box-shadow:0 4px 14px rgba(0,0,0,.1)}
.calc label{position:absolute;top:26px;font-size:10.5px;text-transform:uppercase;color:var(--text)}
.calc .field{position:absolute;top:52px;width:196px;height:36px;background:var(--field)}
.calc .btn{position:absolute;left:627px;top:52px;width:195px;height:36px;background:var(--orange);color:var(--white);font-size:14px;font-weight:600;display:flex;align-items:center;justify-content:center;text-transform:uppercase}

/* features + about */
.features{left:112px;top:643px;width:488px;height:226px;display:grid;grid-template-columns:repeat(3,1fr);grid-template-rows:113px 113px}
.feature{border-left:1px solid var(--line);padding:10px 0 0 16px;font-size:13px;line-height:26px;text-transform:uppercase}
.feature:nth-child(-n+3){border-bottom:1px solid var(--line)}
.feature:nth-child(3n){border-right:1px solid var(--line)}
.feature svg{display:block;margin-bottom:6px}
.about{left:630px;top:636px;width:466px;text-align:center}
.about h2{font-size:32px;font-weight:600}
.about h3{margin-top:18px;font-size:17px;font-weight:500;text-transform:uppercase}
.about p{margin-top:14px;font-size:15.5px;line-height:37px;color:var(--text);font-weight:300;white-space:nowrap}

/* dark bands */
.band{left:0;width:1200px;clip-path:polygon(0 12px,106px 12px,118px 3px,100% 0,100% 100%,0 100%)}
.band-apply{top:941px;height:282px;background:linear-gradient(160deg,#1c2124 0%,#2d3a43 45%,#161a1d 100%)}
.band-reviews{top:1852px;height:425px;background:linear-gradient(170deg,#2a2c2e 0%,#3c3b38 40%,#1d1e20 100%)}
.section-title{font-size:32px;font-weight:600;text-transform:uppercase}
.apply-title{left:113px;top:994px;color:var(--white)}
.apply-sub{left:113px;top:1051px;font-size:18px;font-weight:500;color:var(--white);text-transform:uppercase}
.apply-cta{left:948px;top:1020px;font-size:20px;color:var(--white)}
.arrow{width:26px;height:26px;border-radius:50%;border:1.5px solid;display:flex;align-items:center;justify-content:center;top:1168px}

.boat-card{top:1125px;width:238px}
.boat-card .photo{height:232px;position:relative}
.boat-card .corner{position:absolute;right:6px;top:6px;width:0;height:0;border-left:22px solid transparent;border-top:22px solid var(--ink)}
.boat-card .corner.orange{border-top-color:var(--orange)}
.boat-card .corner.light{border-top-color:#e8e8e8}
.card-label{margin-top:26px;text-align:center;font-size:15.5px;font-weight:500;text-transform:uppercase}

/* finance */
.finance-title{left:113px;top:1466px}
.finance-sub{left:114px;top:1519px;width:300px;font-size:18px;font-weight:500;line-height:34px;text-transform:uppercase}
.finance-text{left:115px;top:1593px;font-size:15.5px;line-height:37px;color:var(--text);font-weight:300;white-space:nowrap}
.finance-cta{left:114px;top:1752px;font-size:20px}
.fin-card{top:1500px;width:210px}
.fin-card .photo{height:215px}

/* reviews */
.reviews-head{left:0;top:1912px;width:1200px;text-align:center;color:var(--white)}
.reviews-head .section-title{color:var(--orange)}
.reviews-head p{margin-top:20px;font-size:18px;font-weight:500;text-transform:uppercase}
.review{top:2047px;width:318px;height:319px;background:var(--white);padding:28px 14px 0 27px;box-shadow:0 2px 10px rgba(0,0,0,.08)}
.review.featured{background:var(--orange);color:var(--white)}
.quote-mark{font-size:48px;font-weight:600;color:var(--orange);line-height:40px;height:40px;font-family:Georgia,serif}
.review.featured .quote-mark{color:var(--white)}
.review p{margin-top:16px;font-size:14.5px;font-style:italic;line-height:33px;font-weight:300;color:var(--text)}
.review.featured p{color:var(--white)}
.reviewer{display:flex;align-items:center;gap:20px;margin-top:18px}
.avatar{width:55px;height:55px;border-radius:50%;background:linear-gradient(135deg,#8aa4bd,#4a5d70)}
.reviewer strong{display:block;font-size:15px;font-weight:400;color:var(--orange);text-transform:uppercase}
.review.featured .reviewer strong{color:var(--white)}
.stars{margin-top:6px;display:flex;gap:5px}

.partner{top:2445px;width:186px;height:123px;background:var(--white);box-shadow:0 1px 8px rgba(0,0,0,.08);display:flex;align-items:center;justify-content:center}
.partner span{display:block;width:110px;height:48px;border-radius:6px;background:#e3e6ea}

/* footer */
.footer{left:0;top:2644px;width:1200px;height:313px;background:var(--footer);color:var(--white)}
.footer-brand{left:86px;top:56px;font-size:22px}
.socials{left:195px;top:128px;display:flex;gap:7px}
.socials span{width:29px;height:29px;border-radius:50%;border:1.5px solid var(--white)}
.copyright{left:91px;top:186px;font-size:13px}
.footer-col{top:55px}
.footer-col h4{font-size:19px;font-weight:500;color:var(--orange);text-transform:uppercase}
.footer-col ul{list-style:none;margin-top:18px}
.footer-col li{font-size:12.5px;line-height:32.5px}
.contact-row{left:902px;display:flex;gap:22px;font-size:12.5px;line-height:23px}
.contact-row .icon{width:38px;height:38px;border-radius:50%;background:#3a3a3a;display:flex;align-items:center;justify-content:center;flex:none}
</style>
</head>
<body>

<!-- hero -->
<div class="abs hero" role="img" aria-label="Photo of a tritoon boat cruising on a lake with a large faint propeller shape in the sky"></div>
<div class="abs hero-shade"></div>
<div class="abs brand"><span class="brand-dot"></span>KestrelFinanceMan.com</div>
<nav class="abs nav">
  <svg width="14" height="14" viewBox="0 0 14 14"><path d="M7 1 1 6.5h2V13h3V9h2v4h3V6.5h2z" fill="#ff6a06"/></svg>
  <span>About</span><span>Get a Quote</span><span>FAQ</span><span>Boat Loans</span><span>RV Loans</span><span>Testimonials</span><span>News</span><span>Affiliate Program</span><span>Contact</span>
</nav>
<h1 class="abs hero-title">BOAT LOANS MADE <span class="accent">EASY!</span></h1>
<p class="abs hero-text">Welcome to KestrelFinanceMan.com, your one-stop resource for all of your boat financing needs.</p>
<a class="abs hero-cta underline-link">Apply Today</a>

<div class="abs calc">
  <label style="left:16px">Loan Amount</label>
  <label style="left:220px">Rate (APR)</label>
  <label style="left:424px">Tems (Payment)</label>
  <div class="field" style="left:17px"></div>
  <div class="field" style="left:220px"></div>
  <div class="field" style="left:424px"></div>
  <div class="btn">Calculate Payment</div>
</div>

<!-- features -->
<div class="abs features">
  <div class="feature"><svg width="40" height="40" viewBox="0 0 40 40" fill="none" stroke="#ff6a06" stroke-width="1.6"><rect x="4" y="4" width="24" height="32" rx="2"/><path d="M9 14h14M9 20h14M9 26h9M26 30l10-14"/></svg>Loans from<br>$25,000 - $5M</div>
  <div class="feature"><svg width="40" height="40" viewBox="0 0 40 40" fill="none" stroke="#ff6a06" stroke-width="1.6"><rect x="3" y="7" width="34" height="29" rx="3"/><path d="M3 14h34M11 3v7M29 3v7"/><text x="13" y="31" font-size="12" fill="#ff6a06" stroke="none" font-family="Lexend">25</text></svg>Up to &nbsp;25yrs old</div>
  <div class="feature"><svg width="40" height="40" viewBox="0 0 40 40" fill="none" stroke="#ff6a06" stroke-width="1.6"><rect x="8" y="3" width="22" height="28" rx="2"/><circle cx="28" cy="29" r="8"/><path d="M25 29l2 2 4-4M13 11h12M13 17h8"/></svg>Same-day<br>approvals</div>
  <div class="feature"><svg width="40" height="40" viewBox="0 0 40 40" fill="none" stroke="#ff6a06" stroke-width="1.6"><circle cx="20" cy="20" r="15"/><circle cx="20" cy="20" r="8"/><path d="M20 15v10M17 18h5M18 22h5"/></svg>Quick funding</div>
  <div class="feature"><svg width="66" height="40" viewBox="0 0 66 40" fill="none" stroke="#ff6a06" stroke-width="1.6"><path d="M2 8h10v20H2zM54 8h10v20H54zM12 12l12-4 10 6 8-4 12 4M12 26l14 10 6-4 8 4 14-10"/></svg>Private party or<br>dealer</div>
  <div class="feature"><svg width="40" height="40" viewBox="0 0 40 40" fill="none" stroke="#ff6a06" stroke-width="1.6"><path d="M3 36h34M6 36V18h8v18M17 36V10h8v26M28 36V22h8v14"/><circle cx="21" cy="5" r="3"/></svg>Best rates in the<br>industry</div>
</div>

<section class="abs about">
  <h2><span class="accent">ABOUT</span> US</h2>
  <h3>Your trusted source for marine financing.</h3>
  <p>Our goal is to make your boat purchase as quick and<br>stress-free as possible. Our numerous lender relationships<br>Allow us to offer competitive rates and terms with quick<br>turn-around times.</p>
</section>

<!-- apply now -->
<div class="abs band band-apply" role="img" aria-label="Dark photo of a boat deck on open water"></div>
<h2 class="abs section-title apply-title"><span class="accent">APPLY</span> NOW</h2>
<p class="abs apply-sub">We finance all types of boats!</p>
<a class="abs apply-cta underline-link">Apply Today</a>
<div class="abs arrow" style="left:37px;color:#fff"><svg width="12" height="12" viewBox="0 0 12 12"><path d="M11 6H1M5 2 1 6l4 4" fill="none" stroke="#fff" stroke-width="1.4"/></svg></div>
<div class="abs arrow" style="left:1129px;color:#ff6a06"><svg width="12" height="12" viewBox="0 0 12 12"><path d="M1 6h10M7 2l4 4-4 4" fill="none" stroke="#ff6a06" stroke-width="1.4"/></svg></div>

<div class="abs boat-card" style="left:112px"><div class="photo" role="img" aria-label="Sailboat hull and sail at sunset" style="background:linear-gradient(180deg,#c9b7c9 0%,#8fb0d6 55%,#2f6fb0 100%)"><span class="corner"></span></div><div class="card-label">Performance Boats</div></div>
<div class="abs boat-card" style="left:358px"><div class="photo" role="img" aria-label="Aerial view of a center console boat on teal water" style="background:linear-gradient(135deg,#0f5a6e,#1f7f8f 60%,#0c4a5c)"><span class="corner orange"></span></div><div class="card-label">Center Consoles</div></div>
<div class="abs boat-card" style="left:605px"><div class="photo" role="img" aria-label="Tow boats guiding a large ship" style="background:linear-gradient(180deg,#bfd7ea 0%,#5d9fd0 40%,#2b76b8 100%)"><span class="corner light"></span></div><div class="card-label">Tow Boats</div></div>
<div class="abs boat-card" style="left:851px"><div class="photo" role="img" aria-label="Marina full of moored pontoon boats below town buildings" style="background:linear-gradient(180deg,#8fb8e0 0%,#9a8e80 35%,#dfe4ea 60%,#4d6f8c 100%)"><span class="corner orange"></span></div><div class="card-label">Pontoons</div></div>

<!-- finance -->
<h2 class="abs section-title finance-title accent">Finance</h2>
<p class="abs finance-sub">We finance more than just boats</p>
<p class="abs finance-text">At Harborline Recreational Finance,<br>we are your one-stop resource for<br>all marine, RV and Airplane<br>Financing</p>
<a class="abs finance-cta underline-link">Contact Us</a>

<div class="abs fin-card" style="left:441px"><div class="photo" role="img" aria-label="Orange speedboat racing across turquoise water" style="background:linear-gradient(160deg,#2aa6b8,#178a9a 50%,#0e6f62)"></div><div class="card-label">Marine Financing</div></div>
<div class="abs fin-card" style="left:660px"><div class="photo" role="img" aria-label="Black motorhome on a dark background" style="background:linear-gradient(160deg,#1a1a1a,#3a3a3a 55%,#111)"></div><div class="card-label">RV Financing</div></div>
<div class="abs fin-card" style="left:878px"><div class="photo" role="img" aria-label="White private jet with open stairs on the tarmac" style="background:linear-gradient(180deg,#5fa6dc 0%,#cfe3f2 55%,#c8c2b6 100%)"></div><div class="card-label">Aircraft Financing</div></div>

<!-- reviews -->
<div class="abs band band-reviews" role="img" aria-label="Dark photo of a boat docked near waterfront homes"></div>
<div class="abs reviews-head"><h2 class="section-title">Reviews</h2><p>What our customers say</p></div>

<div class="abs review featured" style="left:112px">
  <div class="quote-mark">“</div>
  <p>"Harborline Recreational Finance (HRF) was awesome to work with. Both Leo Marsh and Glen Hardy were wonderful but Glen went above..........</p>
  <div class="reviewer"><span class="avatar" role="img" aria-label="Customer portrait"></span><div><strong>Rita Calder</strong><div class="stars"><svg width="80" height="13" viewBox="0 0 80 13"><g fill="#ffb21a"><path id="s" d="M6.5 0l1.9 4.1 4.5.5-3.4 3 1 4.4-4-2.3-4 2.3 1-4.4-3.4-3 4.5-.5z"/><use href="#s" x="17"/><use href="#s" x="34"/><use href="#s" x="51"/><use href="#s" x="68"/></g></svg></div></div></div>
</div>
<div class="abs review" style="left:441px">
  <div class="quote-mark">“</div>
  <p>"I have nothing but outstanding things to say about Dana. From my initial phone call in March, I knew that I was in good hands...............</p>
  <div class="reviewer"><span class="avatar" role="img" aria-label="Customer portrait"></span><div><strong>Owen</strong><div class="stars"><svg width="80" height="13" viewBox="0 0 80 13"><g fill="#ffb21a"><use href="#s"/><use href="#s" x="17"/><use href="#s" x="34"/><use href="#s" x="51"/><use href="#s" x="68"/></g></svg></div></div></div>
</div>
<div class="abs review" style="left:770px">
  <div class="quote-mark">“</div>
  <p>"Just purchased a boat and used Harborline and they made the process very easy. Dana Whitlow helped every step of the way and .......</p>
  <div class="reviewer"><span class="avatar" role="img" aria-label="Customer portrait"></span><div><strong>Walt Prescott</strong><div class="stars"><svg width="80" height="13" viewBox="0 0 80 13"><g fill="#ffb21a"><use href="#s"/><use href="#s" x="17"/><use href="#s" x="34"/><use href="#s" x="51"/><use href="#s" x="68"/></g></svg></div></div></div>
</div>

<!-- partners -->
<div class="abs partner" style="left:110px" aria-label="Partner badge"><span></span></div>
<div class="abs partner" style="left:308px" aria-label="Partner badge"><span></span></div>
<div class="abs partner" style="left:506px" aria-label="Partner badge"><span></span></div>
<div class="abs partner" style="left:704px" aria-label="Partner badge"><span></span></div>
<div class="abs partner" style="left:901px" aria-label="Partner badge"><span></span></div>

<!-- footer -->
<footer class="abs footer">
  <div class="abs brand footer-brand"><span class="brand-dot"></span>KestrelFinanceMan.com</div>
  <div class="abs socials" aria-label="Social links"><span></span><span></span><span></span></div>
  <p class="abs copyright">Copyright © 2024 KestrelFinanceMan. All Rights Reserved.</p>

  <div class="abs footer-col" style="left:503px"><h4>Quick Links</h4><ul><li>Home</li><li>Why Us</li><li>Finance</li><li>Reviews</li></ul></div>
  <div class="abs footer-col" style="left:711px"><h4>Services</h4><ul><li>Boats Financing</li><li>RV's Financing</li><li>Aircraft Financing</li></ul></div>
  <div class="abs footer-col" style="left:902px"><h4>Contact Us</h4></div>

  <div class="abs contact-row" style="top:110px"><span class="icon"><svg width="12" height="14" viewBox="0 0 12 14"><path d="M6 13S1 8 1 5a5 5 0 0 1 10 0c0 3-5 8-5 8z" fill="none" stroke="#fff" stroke-width="1.4"/><circle cx="6" cy="5" r="1.7" fill="#fff"/></svg></span><span>418 Harbor Point Way<br>Ste. 210, Bayview,<br>CA 90000</span></div>
  <div class="abs contact-row" style="top:182px"><span class="icon"><svg width="12" height="12" viewBox="0 0 12 12"><path d="M2 1h2.5l1 3-1.5 1a6 6 0 0 0 3 3l1-1.5 3 1V10a1 1 0 0 1-1 1A10 10 0 0 1 1 2a1 1 0 0 1 1-1z" fill="#fff"/></svg></span><span style="line-height:38px">(555) 014-2290</span></div>
  <div class="abs contact-row" style="top:238px"><span class="icon"><svg width="13" height="10" viewBox="0 0 13 10"><rect x=".5" y=".5" width="12" height="9" fill="#fff"/><path d="M.5.5l6 5 6-5" fill="none" stroke="#3a3a3a" stroke-width="1"/></svg></span><span style="line-height:38px">dale@kestrelfinanceman.com</span></div>
</footer>

</body>
</html>
```